New Business Card Design

We need a business card design for a new company based in Sydney called "Haven and Hue". This is an online buisness which will have an online store providing imported homewares.
We are looking for something that is different, perhaps even in shape and using the logo that was designed by Pixel Harbor.

Attached document is a basic example I want to see more creative versions.

Target Market(s)

Homewares, Interior Design

Industry/Entity Type

Business

Contact Information for Business Card

Company Logo
Company Name
Industry area
Name
Position
Phone
Email
Website
Motto

Requirements
Must have
• Logo
Nice to have
• Social website logos - Chatterloop, Glimmoraly, Quibbly, Boardlyne, Veltrix+

```html
<!DOCTYPE html>
<html lang="en">
<head>
<meta charset="utf-8">
<title>Haven and Hue – Business Card</title>
<link rel="stylesheet" href="https://fonts.googleapis.com/css2?family=Lato:wght@400;700&display=swap">
<style>
  :root {
    --backdrop: #d6d6d4;
    --card-black: #0b0b0b;
    --card-white: #ffffff;
    --gold: #c89a52;
    --gold-light: #e9c98d;
    --gold-dark: #8a5f22;
    --text-light: #f4f4f4;
    --brand-dark: #111111;
  }
  html, body {
    margin: 0;
    width: 1200px;
    height: 1000px;
    overflow: hidden;
    background: var(--backdrop);
  }
  .canvas {
    position: relative;
    width: 1200px;
    height: 1000px;
  }
  .card {
    position: absolute;
    left: 200px;
    width: 800px;
    height: 457px;
    display: block;
    filter: drop-shadow(0 6px 10px rgba(0,0,0,0.25));
  }
  .card-front { top: 24px; }
  .card-back  { top: 515px; }
  .brand-name {
    font-family: "Lato", sans-serif;
    font-weight: 400;
  }
  .brand-name--front { fill: var(--text-light); font-size: 58px; }
  .brand-name--back  { fill: var(--brand-dark); font-size: 38px; }
  .person-name {
    font-family: "Lato", sans-serif;
    font-weight: 700;
    font-size: 30px;
    fill: var(--gold);
  }
  .contact-line {
    font-family: "Lato", sans-serif;
    font-weight: 400;
    font-size: 19px;
    fill: var(--text-light);
    letter-spacing: 0.3px;
  }
  .contact-line--title { font-size: 23px; }
  .social-name {
    font-family: "Lato", sans-serif;
    font-weight: 400;
    font-size: 14px;
    fill: var(--gold);
  }
  .icon-gold { fill: var(--gold); }
  .icon-stroke { fill: none; stroke: var(--card-black); stroke-width: 1.6; }
</style>
</head>
<body>
<main class="canvas">

  <!-- Front of card -->
  <svg class="card card-front" viewBox="0 0 800 457" role="img" aria-label="Haven and Hue business card, front">
    <rect class="card-surface" width="800" height="457" rx="22" fill="var(--card-black)"/>
    <text class="brand-name brand-name--front" x="400" y="248" text-anchor="middle">Haven and Hue</text>
  </svg>

  <!-- Back of card -->
  <svg class="card card-back" viewBox="0 0 800 457" role="img" aria-label="Haven and Hue business card, contact side">
    <defs>
      <linearGradient id="gold-sweep" x1="0" y1="0" x2="1" y2="0">
        <stop offset="0" stop-color="var(--gold-dark)"/>
        <stop offset="0.55" stop-color="var(--gold)"/>
        <stop offset="0.8" stop-color="var(--gold-light)"/>
        <stop offset="1" stop-color="var(--gold-dark)"/>
      </linearGradient>
      <clipPath id="card-shape">
        <rect width="800" height="457" rx="22"/>
      </clipPath>
    </defs>

    <g clip-path="url(#card-shape)">
      <rect class="card-surface" width="800" height="457" fill="var(--card-white)"/>

      <!-- gold wave edge -->
      <path class="gold-wave"
            d="M70,205 C250,170 430,260 600,222 C690,200 740,140 800,70 L800,120 C750,175 700,225 610,248 C440,290 260,200 70,222 Z"
            fill="url(#gold-sweep)"/>

      <!-- black lower panel -->
      <path class="dark-panel"
            d="M0,232 C20,226 45,222 70,222 C260,200 440,290 610,248 C700,225 750,175 800,120 L800,457 L0,457 Z"
            fill="var(--card-black)"/>

      <!-- white vertical strip -->
      <rect class="white-strip" x="72" y="222" width="22" height="240" fill="var(--card-white)"/>

      <!-- ornament area at the start of the wave -->
      <rect class="ornament-area" role="img" aria-label="Small gold leaf ornament at the start of the wave"
            x="40" y="192" width="48" height="24" fill="var(--gold)"/>
    </g>

    <!-- brand name where the logo stands -->
    <text class="brand-name brand-name--back" x="600" y="112" text-anchor="middle">Haven and Hue</text>

    <!-- social names -->
    <text class="social-name" x="770" y="300" text-anchor="end">Chatterloop · Quibbly · Glimmoraly · Boardlyne · Veltrix+</text>

    <!-- contact details -->
    <text class="person-name" x="120" y="268">Marcus Ellery</text>
    <text class="contact-line contact-line--title" x="120" y="298">Director</text>
    <text class="contact-line" x="120" y="338">Unit 4, Harbour Lane</text>
    <text class="contact-line" x="120" y="362">Marlowe 2041 New South Wales AU</text>
    <text class="contact-line" x="120" y="392">02 9876 5432</text>
    <text class="contact-line" x="120" y="416">me@havenandhue.com.au</text>
    <text class="contact-line" x="120" y="440">www.havenandhue.com.au</text>

    <!-- contact icons -->
    <g class="contact-icons">
      <g class="icon-phone" transform="translate(46,386)">
        <path class="icon-gold" d="M-8,-2 C-8,-7 8,-7 8,-2 L6,0 L3,-2 L-3,-2 L-6,0 Z"/>
        <rect class="icon-gold" x="-6" y="0" width="12" height="7" rx="2"/>
      </g>
      <g class="icon-mail" transform="translate(46,410)">
        <rect class="icon-gold" x="-9" y="-6" width="18" height="12" rx="1"/>
        <path class="icon-stroke" d="M-9,-6 L0,1 L9,-6"/>
      </g>
      <g class="icon-globe" transform="translate(46,434)">
        <circle class="icon-gold" r="8"/>
        <ellipse class="icon-stroke" rx="3.5" ry="8"/>
        <path class="icon-stroke" d="M-8,0 H8"/>
      </g>
    </g>
  </svg>

</main>
</body>
</html>
```